Walk Beside The River

Business Card design

Target Market(s)

People who require support in the commnity

Industry/Entity Type

Mental Health Support

Contact Information for Business Card

Mental Health Support Rosalind Tavener walkbesidetheriver@mailcove.com.au 0481 637 092 PO Box 926 Riverbend QLD 4590

Colors
6B429C
8869AF
B7A5CE
E3DAEB
F3F0F8

Requirements
Must have
• Logo & details listed above
Should not have
• No red or orange

```html
<!DOCTYPE html>
<html lang="en">
<head>
<meta charset="utf-8">
<title>Walk Beside The River – Business Card</title>
<link rel="stylesheet" href="https://fonts.googleapis.com/css2?family=Open+Sans:wght@400;600;800&display=swap">
<style>
  :root {
    --purple: #6B429C;
    --purple-mid: #8869AF;
    --lilac: #B7A5CE;
    --yellow: #F2E832;
    --yellow-deep: #E9C93A;
    --ink: #111111;
    --white: #FFFFFF;
    --backdrop: #232323;
  }
  * { box-sizing: border-box; margin: 0; padding: 0; }
  html, body {
    width: 1200px; height: 780px; overflow: hidden;
    background: var(--backdrop);
    font-family: "Open Sans", Arial, sans-serif;
  }
  .stage {
    width: 1200px; height: 780px;
    display: flex; align-items: center; justify-content: center; gap: 40px;
  }
  .card {
    position: relative;
    width: 540px; height: 338px;
    border-radius: 22px;
    overflow: hidden;
  }
  .card-back {
    background: linear-gradient(160deg, #F4EE5A 0%, var(--yellow) 45%, var(--yellow-deep) 100%);
  }
  .card-front { background: var(--white); }
  .brand {
    position: absolute; right: 24px; top: 26px;
    display: flex; align-items: center; gap: 10px;
  }
  .brand-dot {
    width: 56px; height: 56px; border-radius: 50%;
    background: var(--purple);
    flex: none;
  }
  .brand-name {
    font-size: 16px; font-weight: 800; color: var(--purple);
    line-height: 1.2; width: 118px;
  }
  .name-marker {
    position: absolute; left: 0; top: 118px;
    width: 30px; height: 62px;
    background: var(--yellow);
  }
  .name-block { position: absolute; left: 44px; top: 112px; }
  .person-name {
    font-size: 32px; font-weight: 800; color: var(--purple);
    line-height: 1.1;
  }
  .person-role {
    font-size: 15px; font-weight: 600; color: var(--ink); margin-top: 2px;
  }
  .contacts {
    position: absolute; left: 84px; top: 196px;
    list-style: none;
  }
  .contacts li {
    display: flex; align-items: center; gap: 10px;
    font-size: 14px; color: var(--ink); line-height: 22px;
    white-space: nowrap;
  }
  .contacts svg { width: 15px; height: 15px; fill: var(--purple); flex: none; }
  .tagline-band {
    position: absolute; left: 0; right: 0; top: 268px; height: 38px;
    background: var(--yellow);
    display: flex; align-items: center; justify-content: flex-end;
    padding-right: 48px;
    font-size: 15px; font-weight: 600; color: var(--ink);
    white-space: nowrap;
  }
  .edge-band {
    position: absolute; left: 0; right: 0; bottom: 0; height: 12px;
    background: var(--yellow);
  }
</style>
</head>
<body>
<main class="stage">
  <section class="card card-back" role="img" aria-label="Yellow card back covered in a repeating pattern of golden sparkle stars"></section>

  <section class="card card-front">
    <div class="brand">
      <span class="brand-dot"></span>
      <span class="brand-name">Walk Beside The River</span>
    </div>

    <div class="name-marker"></div>
    <div class="name-block">
      <h1 class="person-name">Daniela Vorlova</h1>
      <p class="person-role">CEO/Director</p>
    </div>

    <ul class="contacts">
      <li>
        <svg viewBox="0 0 24 24" aria-hidden="true"><path d="M6.6 10.8a15.1 15.1 0 0 0 6.6 6.6l2.2-2.2a1 1 0 0 1 1-.25 11.4 11.4 0 0 0 3.6.57 1 1 0 0 1 1 1V20a1 1 0 0 1-1 1A17 17 0 0 1 3 4a1 1 0 0 1 1-1h3.5a1 1 0 0 1 1 1c0 1.25.2 2.45.57 3.6a1 1 0 0 1-.25 1z"/></svg>
        0481 637 092
      </li>
      <li>
        <svg viewBox="0 0 24 24" aria-hidden="true"><path d="M3 5h18a1 1 0 0 1 1 1v12a1 1 0 0 1-1 1H3a1 1 0 0 1-1-1V6a1 1 0 0 1 1-1zm9 7.2L20 7H4zM4 9v8h16V9l-8 5.2z"/></svg>
        walkbesidetheriver@mailcove.com.au
      </li>
      <li>
        <svg viewBox="0 0 24 24" aria-hidden="true"><path d="M12 2a7 7 0 0 0-7 7c0 5.2 7 13 7 13s7-7.8 7-13a7 7 0 0 0-7-7zm0 9.5A2.5 2.5 0 1 1 12 6.5a2.5 2.5 0 0 1 0 5z"/></svg>
        PO Box 926 Riverbend QLD 4590
      </li>
    </ul>

    <div class="tagline-band">Mental Health Support Rosalind Tavener</div>
    <div class="edge-band"></div>
  </section>
</main>
</body>
</html>
```